We need a cover designed for our book on parenting. The focus of this book is on the parents, not on the child! We like the idea of this title having a double meaning - insight as in gaining insights into parenting, and "in sight" as in looking inward as parents and how to improve ourselves rather than looking outward to improve our children. We would love for the cover to somehow represent this double meaning. I can upload an excerpt from the book soon over the next few days.

Reason: We are still reviewing the amazing designs! Thank you so much! :)

Target Market(s)

Parents with kids of any age from babies through adult children.

Requirements
Must have
• Title is: Harborlight Parenting
• Subtitle is: Steady Homes, Calmer Hearts Ahead
• Authors names: Lena Marsh, LCSW Oscar Marsh, Ph.D.

```html
<!DOCTYPE html>
<html lang="en">
<head>
<meta charset="utf-8">
<title>Harborlight Parenting — Book Cover</title>
<link rel="stylesheet" href="https://fonts.googleapis.com/css2?family=Poppins:ital,wght@0,600;1,500&family=Oswald:wght@600&display=swap">
<style>
  :root {
    --night: #05070d;
    --night-blue: #1b2a52;
    --title-yellow: #d8d83a;
    --text-white: #ffffff;
    --sky-peach: #e9cfa8;
    --mountain-violet: #7a5f8e;
    --lake-blue: #6f86b4;
    --shore-dark: #2a2230;
  }
  * { margin: 0; padding: 0; box-sizing: border-box; }
  html, body {
    width: 800px; height: 1200px; overflow: hidden;
    background: var(--night);
  }
  .cover {
    position: relative;
    width: 800px; height: 1200px;
    overflow: hidden;
    background:
      radial-gradient(ellipse 520px 700px at 90px 760px, rgba(60,85,150,0.75), rgba(27,42,82,0.35) 55%, transparent 80%),
      radial-gradient(ellipse 400px 300px at 120px 380px, rgba(40,60,110,0.5), transparent 75%),
      var(--night);
    text-align: center;
  }
  .title-main {
    position: absolute; left: 0; right: 0; top: 8px;
    font-family: 'Poppins', sans-serif;
    font-weight: 600;
    font-size: 100px;
    line-height: 1.2;
    color: var(--title-yellow);
    white-space: nowrap;
    letter-spacing: 0;
  }
  .title-sub {
    position: absolute; left: 0; right: 0; top: 152px;
    font-family: 'Poppins', sans-serif;
    font-weight: 600;
    font-size: 118px;
    line-height: 1.2;
    color: var(--text-white);
    white-space: nowrap;
  }
  .subtitle {
    position: absolute; left: 0; right: 0; top: 294px;
    font-family: 'Poppins', sans-serif;
    font-style: italic;
    font-weight: 500;
    font-size: 32px;
    color: var(--text-white);
    text-transform: uppercase;
    white-space: nowrap;
  }
  .binocular-view {
    position: absolute; left: 0; top: 430px;
    width: 800px; height: 450px;
  }
  .authors {
    position: absolute; left: 0; right: 0; top: 1118px;
    font-family: 'Oswald', sans-serif;
    font-weight: 600;
    font-size: 46px;
    color: var(--text-white);
    letter-spacing: 0.5px;
    text-transform: uppercase;
    white-space: nowrap;
  }
</style>
</head>
<body>
  <main class="cover">
    <h1>
      <span class="title-main">HARBORLIGHT</span>
      <span class="title-sub">PARENTING</span>
    </h1>
    <p class="subtitle">Steady Homes, Calmer Hearts Ahead</p>

    <svg class="binocular-view" viewBox="0 430 800 450" xmlns="http://www.w3.org/2000/svg">
      <defs>
        <clipPath id="lens-pair">
          <circle cx="275" cy="653" r="213"/>
          <circle cx="528" cy="653" r="213"/>
        </clipPath>
        <linearGradient id="scene-tones" x1="0" y1="0" x2="0" y2="1">
          <stop offset="0" stop-color="var(--sky-peach)"/>
          <stop offset="0.3" stop-color="#d9b89a"/>
          <stop offset="0.42" stop-color="var(--mountain-violet)"/>
          <stop offset="0.55" stop-color="var(--lake-blue)"/>
          <stop offset="0.75" stop-color="#b9a58f"/>
          <stop offset="1" stop-color="#8f8a78"/>
        </linearGradient>
        <radialGradient id="lens-vignette" cx="0.5" cy="0.5" r="0.6">
          <stop offset="0.75" stop-color="#ffffff" stop-opacity="0"/>
          <stop offset="1" stop-color="#ffffff" stop-opacity="0.35"/>
        </radialGradient>
      </defs>
      <g clip-path="url(#lens-pair)" role="img" aria-label="Photo seen through binoculars: a couple holding hands on a rock, looking across a still lake at purple mountains under a glowing sky">
        <rect x="0" y="430" width="800" height="450" fill="url(#scene-tones)"/>
        <rect x="0" y="430" width="800" height="450" fill="url(#lens-vignette)"/>
      </g>
    </svg>

    <p class="authors">Lena Marsh, LCSW, Oscar Marsh, Ph.D.</p>
  </main>
</body>
</html>
```